Förderverein einer Kirchengemeinde sucht Flyer-Design
Zielgruppe
Wir sind ein Förderverein einer Kirchengemeinde, der sich für die kirchenmusikalische Arbeit einsetzt.
Wir wünschen uns ein niveauvolles und zeitgemäßes/modernes Flyerdesign, das die etablierten Konzertbesucher anspricht, aber vor allem auch Menschen erreicht und überzeugt, die (noch) nichts mit Kirche zu tun haben.
Das Alter der (Haupt-) Zielgruppe (Männer und Frauen) erstreckt sich von 45 bis 70 Jahren.
Aufgabenstellung
Bei der Wahl des Formates würden wir (aus der Sicht von Laien) ein zweimal gefaltetes DIN A4 quer Format nehmen. Aber wir lassen uns gerne überraschen und sind grundsätzlich für andere Lösungen offen.
Bitte den Abschnitt für Adress- und sonstige Dateneintragungen samt Kontodaten so gestalten und platzieren, dass man ihn leicht abtrennen und verschicken kann.
Der Flyer soll Kirchenmusik als lebendig und attraktiv darstellen und neue (jüngere) Mitglieder für den Freundeskreis werben.
Lassen Sie die Bilder sprechen!!

```html
<!DOCTYPE html>
<html lang="de">
<head>
<meta charset="utf-8">
<title>Kirchenmusik braucht Freunde – Innenseite links</title>
<link href="https://fonts.googleapis.com/css2?family=Source+Sans+3:wght@600&family=Nunito+Sans:wght@300;400&display=swap" rel="stylesheet">
<style>
  :root {
    --red: #c1151d;
    --text: #575757;
    --paper: #ffffff;
    --hedge: #3f5a2c;
    --lawn: #7d8a4f;
    --facade: #d9d4c8;
  }
  html, body {
    margin: 0;
    padding: 0;
    width: 1200px;
    height: 848px;
    overflow: hidden;
    background: var(--paper);
  }
  .flyer-page {
    position: relative;
    width: 1200px;
    height: 848px;
    background: var(--paper);
    font-family: "Nunito Sans", sans-serif;
    color: var(--text);
  }
  .photo-column {
    position: absolute;
    left: 0;
    top: 0;
  }
  .headline {
    position: absolute;
    right: 529px;
    top: 100px;
    margin: 0;
    font-family: "Source Sans 3", sans-serif;
    font-weight: 600;
    font-size: 41px;
    line-height: 40px;
    color: var(--red);
    text-align: right;
  }
  .divider {
    position: absolute;
    left: 692px;
    top: 99px;
    width: 2px;
    height: 178px;
    background: var(--red);
  }
  .intro {
    position: absolute;
    left: 714px;
    top: 110px;
    margin: 0;
    font-weight: 300;
    font-size: 19.5px;
    line-height: 29.5px;
    letter-spacing: 0.2px;
  }
  .intro p { margin: 0 0 19px; }
  .contribution-title {
    position: absolute;
    left: 465px;
    top: 338px;
    margin: 0;
    font-family: "Source Sans 3", sans-serif;
    font-weight: 600;
    font-size: 25px;
    color: var(--red);
  }
  .benefit-line {
    position: absolute;
    margin: 0;
    font-weight: 400;
    font-size: 18.3px;
    line-height: 20px;
    white-space: nowrap;
  }
</style>
</head>
<body>
<main class="flyer-page">
  <svg class="photo-column" width="520" height="848" viewBox="0 0 520 848">
    <defs>
      <clipPath id="column-shape">
        <polygon points="0,0 318,0 512,848 0,848"/>
      </clipPath>
      <linearGradient id="recorder-group" x1="0" y1="0" x2="0" y2="1">
        <stop offset="0" stop-color="#324a26"/>
        <stop offset="0.55" stop-color="#5d6a4a"/>
        <stop offset="1" stop-color="#7c7f55"/>
      </linearGradient>
      <linearGradient id="children-choir" x1="0" y1="0" x2="0" y2="1">
        <stop offset="0" stop-color="#2f4a22"/>
        <stop offset="0.5" stop-color="#8f8a3a"/>
        <stop offset="1" stop-color="#6f7145"/>
      </linearGradient>
      <linearGradient id="brass-choir" x1="0" y1="0" x2="0" y2="1">
        <stop offset="0" stop-color="#dcd8cf"/>
        <stop offset="0.6" stop-color="#c9c4ba"/>
        <stop offset="1" stop-color="#b9b4aa"/>
      </linearGradient>
    </defs>
    <g clip-path="url(#column-shape)">
      <rect x="0" y="0" width="520" height="254" fill="url(#recorder-group)" role="img" aria-label="Foto: Flötenensemble mit Blockflöten auf einer Wiese vor einer Hecke"/>
      <rect x="0" y="254" width="520" height="238" fill="url(#children-choir)" role="img" aria-label="Foto: Kinderchor in gelben T-Shirts vor einer Hecke"/>
      <rect x="0" y="492" width="520" height="356" fill="url(#brass-choir)" role="img" aria-label="Foto: Posaunenchor mit Blechblasinstrumenten auf einer Treppe vor einem Gebäude"/>
    </g>
    <polygon points="306,0 318,0 512,848 466,848" fill="#ffffff" opacity="0.35"/>
  </svg>

  <h1 class="headline">Kirchenmusik<br>braucht Freunde</h1>
  <div class="divider"></div>
  <div class="intro">
    <p>Im Jahr 1999 gegründet, unterstützt<br>der Freundeskreis Kirchenmusik die<br>vielfältigen musikalischen Aktivitäten<br>an der St. Anselm-Kirche.</p>
    <p>Wir laden Sie ein, Mitglied zu werden!</p>
  </div>

  <h2 class="contribution-title">Mit Ihrem Beitrag …</h2>

  <p class="benefit-line" style="left:474px; top:398px;">… bereichern Sie Wendelbrucks kulturelle Landschaft durch den Erhalt</p>
  <p class="benefit-line" style="left:503px; top:424px;">und Ausbau unseres hohen kirchenmusikalischen Niveaus</p>

  <p class="benefit-line" style="left:489px; top:469px;">… stärken Sie das Ehrenamt</p>

  <p class="benefit-line" style="left:500px; top:513px;">… ermöglichen Sie der Kantorei, dem Posaunenchor, dem</p>
  <p class="benefit-line" style="left:527px; top:539px;">Kinderchor und dem Flötenensemble regelmäßige Proben-</p>
  <p class="benefit-line" style="left:531px; top:565px;">arbeit, Probenwochenenden und die Anschaffung von</p>
  <p class="benefit-line" style="left:538px; top:592px;">Notenmaterial</p>

  <p class="benefit-line" style="left:527px; top:636px;">… erhalten Sie die historische Heinrich Albrand Orgel von 1748</p>

  <p class="benefit-line" style="left:538px; top:680px;">… fördern Sie die Ausbildung kirchenmusikalischen Nach-</p>
  <p class="benefit-line" style="left:565px; top:707px;">wuchses</p>
</main>
</body>
</html>
```